Business cards to launch an education platform

Hi,
I am looking at having new business cards designed.
I am a startup, developing a web platform for schools and university, the education world. It's an online assessment system.
I would like a card that looks classy, and that is using the colors and the font of my logo.

I have attached:
1) my logo
2) A business card that I have designed quickly so you can have all the information required in the card, but I really don't like it.
3) The font that I am using (Lato Regular) to design my web platform
4) Some screenshots of my web platform so you can have a look at the style that I have.

Target Market(s)

Major market: Education system: Schools and university
Minor markets: Business in general

Industry/Entity Type

Business

Contact Information for Business Card

Clara Fenwick
Director

M: 0437 518 902
E: clara.fenwick@amberLoomSystems.com.au

Requirements
Must have
• The colors of my logo

```html
<!DOCTYPE html>
<html lang="en">
<head>
<meta charset="utf-8">
<title>Amber Loom Systems – Business Cards</title>
<link rel="stylesheet" href="https://fonts.googleapis.com/css2?family=Lato:wght@400;700&family=Roboto+Condensed:wght@400;700&display=swap">
<style>
  :root {
    --backdrop: #9a9a9a;
    --paper: #eef0f2;
    --navy-deep: #0a3d7e;
    --navy-mid: #1362b6;
    --navy-back: #043a74;
    --accent-line: #3fa6dc;
    --brand-ink: #1d3f78;
    --brand-square: #1a5eaa;
    --white: #ffffff;
    --contact-ink: #e6eefb;
  }
  * { box-sizing: border-box; margin: 0; padding: 0; }
  html, body {
    width: 1105px; height: 1200px; overflow: hidden;
    background: var(--backdrop);
  }
  .sheet {
    position: relative; width: 1105px; height: 1200px;
  }
  .card {
    position: absolute; left: 180px; width: 746px; height: 427px;
    overflow: hidden;
  }
  .card--front { top: 128px; background: var(--paper); }
  .card--back {
    top: 645px;
    background: radial-gradient(circle at 72% 55%, #0d57a6 0%, var(--navy-back) 55%);
  }

  /* Front */
  .brand {
    position: absolute; top: 92px; left: 0; width: 100%;
    display: flex; justify-content: center; align-items: center; gap: 18px;
  }
  .brand__square {
    width: 62px; height: 62px; background: var(--brand-square);
  }
  .brand__name {
    font-family: "Lato", sans-serif; font-weight: 400;
    font-size: 36px; letter-spacing: 2px; color: var(--brand-ink);
    line-height: 1;
  }
  .front-band {
    position: absolute; left: 0; top: 0; width: 746px; height: 427px;
  }
  .contact {
    position: absolute; left: 44px; top: 302px;
    list-style: none;
    font-family: "Roboto Condensed", sans-serif; font-weight: 400;
    font-size: 16px; color: var(--contact-ink);
  }
  .contact__item {
    display: flex; align-items: center; gap: 12px; height: 29px;
  }
  .contact__icon { width: 16px; height: 16px; flex: none; }
  .person {
    position: absolute; right: 48px; top: 300px; text-align: right;
    font-family: "Roboto Condensed", sans-serif; font-weight: 700;
    color: var(--white);
  }
  .person__name { font-size: 32px; line-height: 1.15; }
  .person__role { font-size: 23px; line-height: 1.2; }

  /* Back */
  .back-brand {
    position: absolute; left: 58px; top: 286px;
    font-family: "Lato", sans-serif; color: var(--white);
  }
  .back-brand__name {
    font-weight: 400; font-size: 33px; letter-spacing: 2px; line-height: 1.2;
  }
  .back-brand__url {
    font-weight: 400; font-size: 19px; margin-top: 6px;
  }
</style>
</head>
<body>
<main class="sheet">

  <section class="card card--front" aria-label="Business card front">
    <svg class="front-band" viewBox="0 0 746 427" aria-hidden="true">
      <defs>
        <radialGradient id="bandGlow" cx="0.45" cy="0.5" r="0.7">
          <stop offset="0" stop-color="#1670c6"/>
          <stop offset="1" stop-color="#0b3f82"/>
        </radialGradient>
      </defs>
      <path d="M0 262 H622 L643 282 L664 262 H746 V427 H0 Z" fill="url(#bandGlow)"/>
      <path d="M0 256 H620 L643 278 L666 256 H746" fill="none" stroke="var(--accent-line)" stroke-width="4"/>
    </svg>

    <div class="brand">
      <span class="brand__square"></span>
      <span class="brand__name">AMBER LOOM SYSTEMS</span>
    </div>

    <ul class="contact">
      <li class="contact__item">
        <svg class="contact__icon" viewBox="0 0 16 16" aria-hidden="true">
          <rect x="4" y="1" width="8" height="14" rx="1.5" fill="none" stroke="#fff" stroke-width="1.5"/>
          <circle cx="8" cy="12.5" r="0.9" fill="#fff"/>
        </svg>
        <span>0437 518 902</span>
      </li>
      <li class="contact__item">
        <svg class="contact__icon" viewBox="0 0 16 16" aria-hidden="true">
          <rect x="1" y="3.5" width="14" height="9" fill="none" stroke="#fff" stroke-width="1.4"/>
          <path d="M1 3.5 L8 9 L15 3.5" fill="none" stroke="#fff" stroke-width="1.4"/>
        </svg>
        <span>clara.fenwick@amberLoomSystems.com.au</span>
      </li>
      <li class="contact__item">
        <svg class="contact__icon" viewBox="0 0 16 16" aria-hidden="true">
          <circle cx="8" cy="8" r="6.5" fill="none" stroke="#fff" stroke-width="1.4"/>
          <ellipse cx="8" cy="8" rx="2.8" ry="6.5" fill="none" stroke="#fff" stroke-width="1.1"/>
          <path d="M1.5 8 H14.5" stroke="#fff" stroke-width="1.1"/>
        </svg>
        <span>www.amberLoomSystems.com.au</span>
      </li>
    </ul>

    <div class="person">
      <p class="person__name">Clara Fenwick</p>
      <p class="person__role">Director</p>
    </div>
  </section>

  <section class="card card--back" aria-label="Business card back">
    <div class="back-brand">
      <p class="back-brand__name">AMBER LOOM SYSTEMS</p>
      <p class="back-brand__url">amberLoomSystems.com.au</p>
    </div>
  </section>

</main>
</body>
</html>
```